Valdo Capital

We need a corporate style website design for a new company based in Shenzhen's Qianhai Special Economic Development Zone, China. We provide a range of financial services to large international investment companies. Typically these companies invest over 5 million RMB. The company is part of a group that consists of NorthKilns, ValdoTrusts and ValdoEquity. Our location and gateway into Qianhai Special Economic Zone is our core advantage. We would like to see designs that Do Not use purple and orange. The website design should be similar to other websites in this family but different enough to give it a unique style (See attached website links for reference). The final design should communicate financial safety and growth. This website will act partly as a business chamber with connections to the government so we would like it to be diplomatic in style.

www.northkilns.example
www.valdotrusts.example

*Nevegation Bar
Should including Homepage, Financial Product, Team, News.
Could refer to www.valdotrusts.example

*Contact Details

Miss Lan
Address:E 728, North Block, KMO Centre, East Sector, Shenzhen Bright Science Campus
Telephone: +86 0755 63920417
Cellphone: +86 13957280316

* Social Media
Should be grouped like:
1. Weibo QRcode+ Weibo
2. Facebook, Twitter, Linkedin.

Industry/Entity Type

Investment

```html
<!DOCTYPE html>
<html lang="en">
<head>
<meta charset="utf-8">
<title>Valdo Capital</title>
<link href="https://fonts.googleapis.com/css2?family=Arimo:wght@400;700&family=Cinzel:wght@400;600&family=Roboto:wght@300;400&display=swap" rel="stylesheet">
<style>
:root{
  --blue:#2a86b8;
  --blue-dark:#1c6a95;
  --ink:#2b2b2b;
  --muted:#777;
  --line:#e3e3e3;
  --hero-a:#3d4046;
  --hero-b:#5c6168;
  --hero-c:#3f5a78;
  --ticker:#1b1b1b;
  --footer:#252525;
  --white:#fff;
}
*{margin:0;padding:0;box-sizing:border-box}
h1,h2,h3,h4{font-weight:400}
html,body{width:770px;height:1200px;overflow:hidden;background:var(--white)}
body{position:relative;font-family:"Arimo",Arial,sans-serif;color:var(--ink)}
.abs{position:absolute}

/* header */
.site-header{left:0;top:0;width:770px;height:53px;background:var(--white)}
.brand{left:100px;top:15px}
.brand-name{font-family:"Cinzel",serif;font-size:18px;font-weight:600;color:#1a1a1a;letter-spacing:.3px}
.main-nav{left:380px;top:17px;display:flex;gap:20px;align-items:center}
.main-nav a{font-family:"Cinzel",serif;font-size:9px;color:#333;text-decoration:none;letter-spacing:.3px}
.main-nav a.active{background:var(--blue);color:var(--white);padding:4px 10px;border-radius:2px}

/* hero */
.hero{left:0;top:53px;width:770px;height:352px;background:linear-gradient(135deg,var(--hero-a) 0%,var(--hero-b) 35%,var(--hero-c) 55%,var(--hero-b) 75%,var(--hero-a) 100%)}
.hero-title{left:0;top:72px;width:770px;text-align:center;font-family:"Cinzel",serif;font-weight:400;font-size:33px;color:var(--white);letter-spacing:1px}
.team-faces{left:281px;top:119px;display:flex;gap:12px}
.team-faces span{width:60px;height:60px;border-radius:50%;border:3px solid var(--white);background:#c9c2b8}
.hero-lede{left:0;top:187px;width:770px;text-align:center;font-size:13px;line-height:15px;color:var(--white)}
.hero-btn{left:350px;top:228px;width:70px;height:22px;background:linear-gradient(#3c9fd0,var(--blue-dark));color:var(--white);font-size:10.5px;text-align:center;line-height:22px;border-radius:2px}
.know-more{left:430px;top:253px;font-family:"Cinzel",serif;font-size:10px;color:var(--white)}
.hero-arrow{top:150px}
.dots{left:362px;top:302px;display:flex;gap:5px}
.dots span{width:8px;height:8px;border-radius:50%;background:#ddd}
.dots span.on{background:var(--blue)}

/* welcome */
.welcome{left:97px;top:381px;width:576px;height:184px;background:var(--white);border-top:3px solid var(--blue);box-shadow:0 1px 4px rgba(0,0,0,.12);text-align:center}
.welcome h2{font-family:"Roboto",sans-serif;font-weight:300;font-size:17px;color:#333;margin-top:26px}
.welcome h1{font-family:"Roboto",sans-serif;font-weight:300;font-size:27px;color:var(--blue);line-height:28px}
.welcome p{font-size:6.4px;line-height:8.7px;color:#444;margin:8px 30px 0}

/* products */
.products{left:123px;top:566px;width:522px;height:180px;border:1px solid var(--line);background:var(--white)}
.card{top:15px;width:112px}
.card-photo{width:112px;height:78px}
.card h3{font-family:"Roboto",sans-serif;font-weight:400;font-size:10.5px;color:var(--blue);margin-top:7px}
.card p{font-size:5.5px;line-height:8.6px;color:#888;margin-top:4px}
.card .more{display:inline-block;margin-top:4px;font-size:5.5px;color:var(--blue);background:#f1f1f1;padding:2px 5px}
.card .more.dark{background:#111;color:var(--white)}
.side-tab{top:641px;width:16px;height:28px;background:var(--blue)}

/* three columns */
.skyline{left:0;top:930px;width:770px;height:114px;background:linear-gradient(rgba(230,232,235,0),#e4e6e9)}
.col-title{font-family:"Roboto",sans-serif;font-weight:400;font-size:11px;color:#222}
.quote{width:164px;height:50px;background:var(--blue);color:var(--white);font-size:6px;line-height:8px;padding:8px 14px}
.quote b{display:block;font-weight:400}
.writer{font-size:6.5px;color:#222;text-align:right;width:164px}
.news-date{font-size:6.5px;color:#333}
.news-head{font-size:6.5px;font-weight:700;color:var(--blue-dark)}
.news-body{font-size:5.8px;line-height:8.4px;color:#888;width:140px}
.news-more{font-size:6.5px;color:var(--blue)}
.col-rule{width:1px;background:var(--line)}
.tweet{width:130px;font-size:5.8px;line-height:8.8px;color:#777}
.tweet a{color:var(--blue);text-decoration:none}
.tweet i{color:#333}
.tweet-dot{width:10px;height:10px;border-radius:50%;background:#555}

/* ticker */
.ticker{left:0;top:1044px;width:770px;height:41px;background:var(--ticker)}
.ticker-title{left:107px;top:13px;font-size:11px;color:var(--white)}
.ticker-bar{left:247px;top:11px;width:415px;height:22px;background:#2c2c2c;border:1px solid #3a3a3a;font-size:7px;line-height:20px;color:#9a9a9a}
.ticker-bar span{color:var(--blue);margin-left:14px}
.ticker-btn{left:636px;top:11px;width:26px;height:22px;background:#000}

/* footer */
.site-footer{left:0;top:1085px;width:770px;height:115px;background:var(--footer)}
.contact{top:26px;display:flex;align-items:center;gap:9px;color:var(--white)}
.contact-ico{width:22px;height:22px;border-radius:50%;background:var(--blue);display:flex;align-items:center;justify-content:center}
.foot-rule{left:107px;top:76px;width:556px;height:1px;background:#333}
.foot-nav{left:107px;top:86px;display:flex;gap:10px;font-size:6.3px;color:var(--white)}
.foot-nav .on{color:var(--blue)}
.copy{left:107px;top:99px;font-size:5px;color:#888}
.stay{left:543px;top:91px;font-family:"Cinzel",serif;font-size:9px;color:var(--white)}
.social{left:604px;top:87px;display:flex;gap:4px}
.social span{width:16px;height:16px;border-radius:50%;background:var(--blue)}
.social span:first-child{background:var(--white)}
</style>
</head>
<body>

<header class="site-header abs">
  <div class="brand abs"><span class="brand-name">Valdo Capital</span></div>
  <nav class="main-nav abs">
    <a class="active" href="#">Home</a>
    <a href="#">Financial Product</a>
    <a href="#">Team</a>
    <a href="#">News</a>
    <a href="#">Contact Us</a>
  </nav>
</header>

<section class="hero abs" role="img" aria-label="Photo of a dark keyboard with a blue currency key">
  <h1 class="hero-title abs">Lorem ipsum dolor sit amet</h1>
  <div class="team-faces abs" role="img" aria-label="Portrait photos of three team members"><span></span><span></span><span></span></div>
  <p class="hero-lede abs">Lorem ipsum dolor sit amet, consectetur adipiscing elit. Nulla<br>lobortis consequat mauris, eget eleifend nunc</p>
  <div class="hero-btn abs">Click Here</div>
  <div class="know-more abs">&#8592; Know More</div>
  <svg class="hero-arrow abs" style="left:57px" width="18" height="40" viewBox="0 0 18 40"><path d="M16 2 L3 20 L16 38" fill="none" stroke="#fff" stroke-width="1.5"/></svg>
  <svg class="hero-arrow abs" style="left:697px" width="18" height="40" viewBox="0 0 18 40"><path d="M2 2 L15 20 L2 38" fill="none" stroke="#fff" stroke-width="1.5"/></svg>
  <div class="dots abs"><span class="on"></span><span></span><span></span><span></span></div>
</section>

<section class="welcome abs">
  <h2>Welcome to</h2>
  <h1>Valdo Capital</h1>
  <p>Lorem ipsum dolor sit amet, consectetur adipiscing elit. Nulla lobortis consequat mauris, eget eleifend nunc viverra viverra. Ut ac risus odio. Aliquam pretium purus sed nulla feugiat blandit. Cras vel libero ut lacus eleifend tempor. Ut ac risus odio. Aliquam pretium purus sed</p>
  <p>Phasellus eleifend, magna non tincidunt accumsan, justo arcu cursus ipsum, non porttitor sapien quam vel magna. Maecenas elit nisl, molestie nec dapibus nec, aliquet a erat. Donec scelerisque lacus a libero suscipit auctor volutpat enim euismod. Mauris porta, lacus ut ullamcorper sodales, mauris tortor feugiat purus, nec aliquam neque purus ac metus. Nunc eleifend leo quis nisl hendrerit ultrices. Suspendisse quis feugiat elit. Fusce vitae dolor ac est tincidunt feugiat. Phasellus volutpat dui in sapien malesuada tempus placerat justo ultricies. Duis mollis ornare risus, ut consectetur mi tincidunt sit amet. Maecenas quis nibh ac. Ut ac risus odio. Aliquam pretium purus sed orci tempus scelerisque ac et massa.</p>
</section>

<div class="side-tab abs" style="left:109px;border-radius:8px 0 0 8px"></div>
<div class="side-tab abs" style="left:645px;border-radius:0 8px 8px 0"></div>

<section class="products abs">
  <article class="card abs" style="left:15px">
    <div class="card-photo" role="img" aria-label="Photo of a businesswoman holding glowing currency symbols" style="background:linear-gradient(135deg,#2a2a2a,#8a7a68)"></div>
    <h3>Lorem ipsum dolor</h3>
    <p>Sit amet, consectetur adipiscing elit. Nulla lobortis consequat mauris, eget eleifend nunc viverra viverra. Ut ac risus odio. Aliquam pretium purus sed nulla.</p>
    <span class="more">Read more</span>
  </article>
  <article class="card abs" style="left:142px">
    <div class="card-photo" role="img" aria-label="Photo of a city skyline" style="background:linear-gradient(#dfe7ec,#8fa3ad)"></div>
    <h3>Lorem ipsum dolor</h3>
    <p>Sit amet, consectetur adipiscing elit. Nulla lobortis consequat mauris, eget eleifend nunc viverra viverra. Ut ac risus odio. Aliquam pretium purus sed nulla.</p>
    <span class="more">Read more</span>
  </article>
  <article class="card abs" style="left:269px">
    <div class="card-photo" role="img" aria-label="Photo of a couple reviewing documents on a sofa" style="background:linear-gradient(135deg,#e8e2dc,#9eb4c8)"></div>
    <h3>Lorem ipsum dolor</h3>
    <p>Sit amet, consectetur adipiscing elit. Nulla lobortis consequat mauris, eget eleifend nunc viverra viverra. Ut ac risus odio. Aliquam pretium purus sed nulla.</p>
    <span class="more">Read more</span>
  </article>
  <article class="card abs" style="left:396px">
    <div class="card-photo" role="img" aria-label="Photo of glasses resting on a newspaper" style="background:linear-gradient(135deg,#f4efe8,#c8b9a4)"></div>
    <h3>Lorem ipsum dolor</h3>
    <p>Sit amet, consectetur adipiscing elit. Nulla lobortis consequat mauris, eget eleifend nunc viverra viverra. Ut ac risus odio. Aliquam pretium purus sed nulla.</p>
    <span class="more dark">Read more</span>
  </article>
</section>

<div class="skyline abs" role="img" aria-label="Faint city skyline backdrop"></div>

<h4 class="col-title abs" style="left:122px;top:789px">Clients Testimonials</h4>
<div class="quote abs" style="left:124px;top:806px"><b>21-03-2014</b>"Lorem ipsum dolor sit amet, consectetur adipiscing elit. Nulla lobortis consequat mauris, eget eleifend nunc viverra consequat mauris."</div>
<div class="writer abs" style="left:124px;top:866px">Writer Name</div>
<div class="quote abs" style="left:124px;top:883px"><b>21-03-2014</b>"Lorem ipsum dolor sit amet, consectetur adipiscing elit. Nulla lobortis consequat mauris, eget eleifend nunc viverra consequat mauris."</div>
<div class="writer abs" style="left:124px;top:943px">Writer Name</div>

<div class="col-rule abs" style="left:310px;top:782px;height:165px"></div>
<h4 class="col-title abs" style="left:334px;top:789px">Latest News</h4>
<div class="news-date abs" style="left:334px;top:810px">15/10/2014:</div>
<div class="news-head abs" style="left:334px;top:822px">Duis nec augue eget lorem vestibulum</div>
<div class="news-body abs" style="left:334px;top:832px">Lorem ipsum dolor sit amet, consectetur adipiscing elit. Nulla lobortis consequat mauris, eget eleifend nunc viverra consequat mauris...</div>
<div class="news-more abs" style="left:454px;top:857px">more</div>
<div class="abs" style="left:334px;top:870px;width:150px;height:1px;background:var(--line)"></div>
<div class="news-date abs" style="left:334px;top:879px">18/10/2014:</div>
<div class="news-head abs" style="left:334px;top:891px">Duis nec augue eget lorem vestibulum</div>
<div class="news-body abs" style="left:334px;top:901px">Lorem ipsum dolor sit amet, consectetur adipiscing elit. Nulla lobortis consequat mauris, eget eleifend nunc viverra consequat mauris...</div>
<div class="news-more abs" style="left:454px;top:926px">more</div>
<div class="news-date abs" style="left:334px;top:944px">All the news</div>

<div class="col-rule abs" style="left:497px;top:782px;height:165px"></div>
<h4 class="col-title abs" style="left:515px;top:790px">Latest Tweets</h4>
<span class="tweet-dot abs" style="left:513px;top:809px"></span>
<p class="tweet abs" style="left:529px;top:805px">Lorem ipsum dolor sit amet, consectetu adipiscing elit, sed diam nonummy nibh<br><a>http://valdocapital.example/</a><br><i>24 minutes ago</i></p>
<span class="tweet-dot abs" style="left:513px;top:853px"></span>
<p class="tweet abs" style="left:529px;top:849px">Lorem ipsum dolor sit amet, consectetu adipiscing elit, sed diam nonummy nibh<br><a>http://valdocapital.example/</a><br><i>26 minutes ago</i></p>
<span class="tweet-dot abs" style="left:513px;top:898px;background:var(--blue)"></span>
<p class="tweet abs" style="left:529px;top:894px">Lorem ipsum dolor sit amet, consecte adipiscing elit, sed diam nonummy<br><a>http://valdocapital.example/</a><br><i>29 minutes ago</i></p>

<section class="ticker abs">
  <div class="ticker-title abs">Valdo Capital in the news</div>
  <div class="ticker-bar abs"><span style="color:#9a9a9a;margin-left:11px">March 05, 2014</span><span>Donec a lectus non purus ultricies eleifend. Duis nec augue eget lorem vestibulum suscipit.</span></div>
  <div class="ticker-btn abs"><svg width="26" height="22" viewBox="0 0 26 22"><path d="M12 7 L8 11 L12 15Z M15 7 L19 11 L15 15Z" fill="#fff"/></svg></div>
</section>

<footer class="site-footer abs">
  <div class="contact abs" style="left:107px"><span class="contact-ico"><svg width="11" height="11" viewBox="0 0 12 12"><path d="M3 1 L5 3.5 L4 5 Q5 7 7 8 L8.5 7 L11 9 L9.5 11 Q4 10.5 1 2.5Z" fill="#fff"/></svg></span><span style="font-size:15px">0000 0000 000</span></div>
  <div class="contact abs" style="left:285px"><span class="contact-ico"><svg width="11" height="8" viewBox="0 0 11 8"><rect x=".5" y=".5" width="10" height="7" fill="none" stroke="#fff"/><path d="M.5 .5 L5.5 4.5 L10.5 .5" fill="none" stroke="#fff"/></svg></span><span style="font-size:11px">support@valdocapital.example</span></div>
  <div class="contact abs" style="left:498px"><span class="contact-ico"><svg width="11" height="9" viewBox="0 0 11 9"><rect x="1" y="3" width="9" height="5.5" rx="1" fill="#fff"/><path d="M1 3 Q5.5 -1 10 3" fill="none" stroke="#fff"/></svg></span><span style="font-size:11px">support@valdocapital.example</span></div>
  <div class="foot-rule abs"></div>
  <nav class="foot-nav abs"><span class="on">Home</span><span>Financial Product</span><span>Team</span><span>News</span><span>Contact Us</span></nav>
  <div class="copy abs">COPYRIGHT © 2014 Valdo Capital Limited. TERMS OF USE | PRIVACY POLICY</div>
  <div class="stay abs">Stay with us</div>
  <div class="social abs"><span></span><span></span><span></span></div>
</footer>

</body>
</html>
```